Redesign Website - Current one too plain

The description is in the uploaded file. Please let me know if you need any more information. I'd prefer it if someone could implement the design to a WordPress site but the best design will win, regardless.
I would like the forms to look nice as well
UPDATE:
I don't think we can use the images that I provided, I think they make the site look a bit 'cheap' and I really don't know how to replace them. One thought I have had is to make the "Simple, Unique, Effective" a second feature on the right side of the page with the search on the left
Target Market(s)
Small companies, private sellers of cars and people who rent their caravan/holiday home out
Industry/Entity Type
Advertising
Number of Pages Required
3 page
Colors
Designer to choose colors to be used in the design.
Look and feel
Each slider illustrates characteristics of the customer's brand and the style your logo design should communicate.

```html
<!DOCTYPE html>
<html lang="en">
<head>
<meta charset="UTF-8">
<title>VELDO — Contact Us</title>
<link rel="stylesheet" href="https://fonts.googleapis.com/css2?family=Urbanist:wght@400;500;600;700&display=swap">
<style>
  :root {
    --lime: #e3fb17;
    --lime-text: #b7d92b;
    --ink: #151515;
    --muted: #a9a5a7;
    --field: #f7f3f4;
    --bg: #ffffff;
    --forest: #2f7a54;
    --forest-dark: #1f6b47;
    --sky: #9ec7ca;
    --hill: #6f8a8f;
  }
  * { box-sizing: border-box; margin: 0; padding: 0; }
  html, body { width: 1200px; height: 1090px; overflow: hidden; background: var(--bg); }
  body { font-family: "Urbanist", sans-serif; color: var(--ink); position: relative; }

  .site-header { position: absolute; left: 161px; top: 31px; width: 878px; height: 41px; display: flex; align-items: center; justify-content: space-between; }
  .brand { display: flex; align-items: center; gap: 8px; font-size: 24px; font-weight: 500; letter-spacing: 3px; color: var(--lime-text); }
  .brand-dot { width: 22px; height: 22px; border-radius: 50%; background: var(--lime-text); }
  .main-nav { position: absolute; left: 310px; display: flex; gap: 20px; font-size: 14px; font-weight: 500; }
  .main-nav a { color: var(--ink); text-decoration: none; }
  .main-nav a.is-active { color: var(--lime-text); font-weight: 600; }
  .login-button { width: 130px; height: 41px; border-radius: 21px; background: var(--lime); display: flex; align-items: center; justify-content: center; font-size: 15px; font-weight: 500; color: var(--ink); text-decoration: none; }

  .hero-banner { position: absolute; left: 21px; top: 107px; width: 1159px; height: 281px; border-radius: 16px;
    background: linear-gradient(160deg, #2b8a5a 0%, var(--forest-dark) 45%, var(--forest) 100%); }

  .contact-section { position: absolute; left: 161px; top: 429px; width: 446px; }
  .contact-title { font-size: 33px; font-weight: 400; line-height: 1; margin-top: 8px; }
  .contact-title strong { font-weight: 700; }
  .field-label { display: block; font-size: 17px; font-weight: 500; margin-top: 31px; margin-bottom: 19px; line-height: 1; }
  .field-label.first { margin-top: 34px; }
  .field-input { display: block; width: 446px; height: 56px; border: none; border-radius: 14px; background: var(--field); padding: 0 35px; font-family: inherit; font-size: 13px; color: var(--ink); }
  .field-input::placeholder, .field-area::placeholder { color: var(--muted); }
  .field-area { display: block; width: 446px; height: 143px; border: none; border-radius: 14px; background: var(--field); padding: 18px 35px; font-family: inherit; font-size: 13px; resize: none; }
  .submit-button { margin-top: 34px; margin-left: 2px; width: 156px; height: 42px; border: none; border-radius: 21px; background: var(--lime); display: flex; align-items: center; justify-content: space-between; padding: 0 22px 0 34px; font-family: inherit; font-size: 15px; font-weight: 600; color: var(--ink); }

  .feature-art { position: absolute; left: 641px; top: 429px; width: 398px; height: 575px; border-radius: 12px;
    background: linear-gradient(180deg, var(--sky) 0%, #dbe9e8 45%, var(--hill) 62%, #e0a13a 70%, #7c7d7a 78%, #5f605e 100%); }

  .site-footer { position: absolute; left: 162px; top: 1043px; width: 875px; display: flex; justify-content: space-between; font-size: 15px; }
  .site-footer strong { font-weight: 700; }
  .legal-links a { color: var(--ink); text-decoration: none; font-weight: 500; }
  .legal-links span { margin: 0 6px; }
</style>
</head>
<body>
  <header class="site-header">
    <div class="brand"><span class="brand-dot"></span>VELDO</div>
    <nav class="main-nav">
      <a href="#" class="is-active">Home</a>
      <a href="#">Advertise</a>
      <a href="#">Contact</a>
      <a href="#">Register</a>
    </nav>
    <a href="#" class="login-button">LOGIN</a>
  </header>

  <div class="hero-banner" role="img" aria-label="Illustration of a winding road through a green forest at night, seen from above"></div>

  <section class="contact-section">
    <h1 class="contact-title">Contact <strong>Us</strong></h1>
    <form>
      <label class="field-label first" for="full-name">Full Name</label>
      <input class="field-input" id="full-name" type="text" placeholder="Enter Your Full Name.">
      <label class="field-label" for="email">Email Address</label>
      <input class="field-input" id="email" type="email" placeholder="Enter Your Email Address.">
      <label class="field-label" for="message">Message</label>
      <textarea class="field-area" id="message" placeholder="Enter Your Message"></textarea>
      <button class="submit-button" type="button">Submit
        <svg width="18" height="14" viewBox="0 0 18 14" aria-hidden="true"><path d="M1 7h15M10 1l6 6-6 6" fill="none" stroke="#151515" stroke-width="1.8" stroke-linecap="round" stroke-linejoin="round"/></svg>
      </button>
    </form>
  </section>

  <div class="feature-art" role="img" aria-label="Illustration of cars driving on a highway through autumn hills and mountains"></div>

  <footer class="site-footer">
    <p>© 2023 <strong>VELDO.</strong> All rights reserved.</p>
    <p class="legal-links"><a href="#">Terms &amp; Conditions</a><span>|</span><a href="#">Privacy Policy</a></p>
  </footer>
</body>
</html>
```